Tolvane Inc., a third party debt collection agency needs a Website

Tolvane needs a very basic website (3 basic pages) so that consumers can download forms, potential employees can get required EEO language and see potential jobs, and to show that they are a consumer friendly organization.

I've attached a list of requirements and wishes titled "Tolvane Website Specifications"

Target Market(s)

Consumers that need to repay their government loans; Tolvane will walk through the process to assist them.

Industry/Entity Type

Financial Service

Coding

Coded - Design and coding required

Number of Pages Required

1 page

Font styles to use
Sans Serif

Colors
0355a3

Requirements
Must have
• Tolvane Logo
• See document "Tolvane Website Specifications" for all requirements

```html
<!DOCTYPE html>
<html lang="en">
<head>
<meta charset="utf-8">
<title>Tolvane Inc.</title>
<link href="https://fonts.googleapis.com/css2?family=Open+Sans:wght@400;600;700&display=swap" rel="stylesheet">
<style>
:root{
  --navy:#262a6f;
  --navy-title:#1d2f66;
  --maroon:#8a1b1d;
  --text:#444;
  --muted:#666;
  --rule:#e4e4e4;
  --white:#fff;
}
*{box-sizing:border-box;margin:0;padding:0}
html,body{width:959px;height:1200px;overflow:hidden;background:var(--white)}
body{position:relative;font-family:"Open Sans",Arial,sans-serif;color:var(--text)}
.abs{position:absolute}
.top-rule{left:0;top:0;width:959px;height:2px;background:var(--navy)}
.brand{left:128px;top:44px;font-weight:700;font-size:25px;color:var(--maroon);letter-spacing:-.3px;display:flex;align-items:center;gap:8px}
.brand .dot{width:12px;height:12px;background:var(--navy);border-radius:50%}
.contact-line{top:20px;font-size:9.6px;color:#555;display:flex;align-items:center;gap:7px;white-space:nowrap}
.icon-ring{width:20px;height:20px;border:1.5px solid var(--maroon);border-radius:50%;display:flex;align-items:center;justify-content:center;flex:none}
.nav{top:67px;font-size:10.4px;font-weight:600;color:#333;letter-spacing:.2px}
.nav.active{color:var(--navy)}
.nav-underline{left:345px;top:82px}
.search{left:800px;top:60px;width:29px;height:29px;border-radius:50%;background:var(--navy);display:flex;align-items:center;justify-content:center}
.header-shadow{left:0;top:98px;width:959px;height:1px;background:#ddd}
.hero{left:0;top:99px;width:959px;height:405px;background:linear-gradient(100deg,#c9c2b8 0%,#e8e2da 28%,#d9dde2 50%,#b8bec6 75%,#8d949c 100%)}
.hero-wave{left:0;top:99px}
.caption-title{left:614px;top:249px;width:345px;height:37px;background:rgba(70,70,70,.85);clip-path:polygon(0 0,100% 0,100% 100%,12px 100%);color:#fff;font-weight:700;font-size:15px;padding:8px 0 0 24px}
.caption-text{left:450px;top:292px;width:509px;height:44px;background:rgba(110,110,110,.8);clip-path:polygon(6px 0,100% 0,100% 100%,0 100%);color:#fff;font-size:8.6px;line-height:12.5px;padding:8px 0 0 24px}
.welcome-title{left:0;top:514px;width:959px;text-align:center;font-size:24px;font-weight:700;color:var(--navy-title)}
.accent{color:var(--maroon)}
.welcome-text{left:150px;top:555px;width:659px;text-align:center;font-size:8.5px;line-height:15.6px;color:var(--text)}
.btn{display:flex;height:25px;font-size:8.5px;font-weight:600;color:#fff;box-shadow:0 1px 2px rgba(0,0,0,.3)}
.btn .label{background:var(--maroon);padding:0 10px;display:flex;align-items:center}
.btn .arrow{background:var(--navy);width:24px;display:flex;align-items:center;justify-content:center}
.divider{left:128px;top:677px;width:702px;height:1px;background:var(--rule)}
.section-title{top:697px;font-size:18px;font-weight:700;color:var(--navy)}
.thumb{width:158px;height:131px;border:3px solid #fff;box-shadow:0 0 3px rgba(0,0,0,.35)}
.thumb-meeting{background:linear-gradient(135deg,#7a7470,#b9b3ab 50%,#d5d8dc)}
.thumb-team{background:linear-gradient(135deg,#3d4a63,#c8c5bf 55%,#e6e2da)}
.col-text{width:166px;top:735px;font-size:8.3px;line-height:15px;color:var(--muted)}
.col-text span{display:block;white-space:nowrap;text-align:justify;text-align-last:justify}
.col-text span.last{text-align-last:left}
.footer{left:0;top:905px;width:959px;height:146px;background:var(--navy)}
.footer-brand{left:128px;top:972px;color:#fff;font-weight:700;font-size:25px;display:flex;align-items:center;gap:8px}
.footer-brand .dot{width:12px;height:12px;background:#fff;border-radius:50%}
.vrule{top:936px;width:1px;height:100px;background:rgba(255,255,255,.2)}
.footer-head{top:933px;color:#fff;font-size:12px;font-weight:600}
.footer-link{left:424px;color:#fff;font-size:9px}
.footer-item{left:686px;color:#fff;font-size:8.6px;line-height:16px;display:flex;gap:8px}
.footer-item svg{margin-top:4px;flex:none}
.copy-bar{left:0;top:1051px;width:959px;height:43px;background:var(--maroon);color:#fff;font-size:8.6px;text-align:center;padding-top:15px}
.badge-a{left:414px;top:1110px;width:58px;height:72px;background:#e7eef7;border:1px solid #9fb6d6}
.badge-a::before{content:"";position:absolute;left:14px;top:6px;width:28px;height:28px;background:#4f86c6}
.badge-b{left:492px;top:1106px;width:44px;height:72px;border-radius:4px;background:#e3ecef;border:1px solid #7fa3ad}
.badge-b::before{content:"";position:absolute;left:12px;top:8px;width:18px;height:30px;border-radius:9px;background:#1d5d72}
</style>
</head>
<body>
<div class="abs top-rule"></div>

<header>
  <div class="abs brand"><span class="dot"></span>Tolvane Inc.</div>
  <div class="abs contact-line" style="left:500px">
    <span class="icon-ring"><svg width="9" height="7" viewBox="0 0 9 7"><rect width="9" height="7" fill="#8a1b1d"/><path d="M0 0 L4.5 4 L9 0" stroke="#fff" fill="none"/></svg></span>
    Email: hello@tolvane.example
  </div>
  <div class="abs contact-line" style="left:707px">
    <span class="icon-ring"><svg width="9" height="9" viewBox="0 0 10 10"><path d="M2 0 L4 2.5 L3 4 Q4.5 6 6 7 L7.5 6 L10 8 L8.5 10 Q3 9 0 2 Z" fill="#8a1b1d"/></svg></span>
    Phone: 555-010-0142
  </div>
  <nav>
    <span class="abs nav active" style="left:347px">HOME</span>
    <svg class="abs nav-underline" width="36" height="8" viewBox="0 0 36 8"><path d="M2 3 Q18 9 34 3" stroke="#262a6f" stroke-width="2" fill="none"/></svg>
    <span class="abs nav" style="left:415px">CONSUMER INFORMATION</span>
    <span class="abs nav" style="left:584px">CAREERS @ TOLVANE</span>
    <span class="abs nav" style="left:730px">CONTACT</span>
    <span class="abs search"><svg width="10" height="10" viewBox="0 0 10 10"><circle cx="4" cy="4" r="3" stroke="#fff" stroke-width="1.5" fill="none"/><path d="M6.2 6.2 L9 9" stroke="#fff" stroke-width="1.6"/></svg></span>
  </nav>
  <div class="abs header-shadow"></div>
</header>

<section>
  <div class="abs hero" role="img" aria-label="Photo of smiling call centre agents wearing headsets in a bright office"></div>
  <svg class="abs hero-wave" width="959" height="405" viewBox="0 0 959 405">
    <path d="M0 353 C140 395 260 410 400 398 C560 385 680 335 830 337 C880 338 920 343 959 352 L959 405 L0 405 Z" fill="#fff"/>
    <path d="M0 353 C140 395 260 410 400 398 C560 385 680 335 830 337 C880 338 920 343 959 352" stroke="#262a6f" stroke-width="3" fill="none"/>
    <path d="M54 161 L34 183 L54 205" stroke="#fff" stroke-width="1.2" fill="none"/>
    <path d="M905 161 L925 183 L905 205" stroke="rgba(255,255,255,.4)" stroke-width="1.2" fill="none"/>
    <rect x="851" y="278" width="26" height="2" fill="#8a1b1d"/>
    <rect x="864" y="284" width="12" height="2" fill="#fff"/>
    <rect x="864" y="290" width="12" height="2" fill="#fff"/>
    <rect x="864" y="296" width="12" height="2" fill="#fff"/>
  </svg>
  <div class="abs caption-title">WELCOME TO TOLVANE</div>
  <div class="abs caption-text">Lorem ipsum dolor sit amet, consectetur adipiscing elit, sed do eiusmod tempornc<br>ididunt ut labore et dolore magna aliqua. Ut enim ad minim veniam.</div>
</section>

<section>
  <h1 class="abs welcome-title">Welcome to <span class="accent">Tolvane</span></h1>
  <p class="abs welcome-text">Tolvane is a third party debt collection agency that is focused on the collection of higher education loans.&nbsp; Tolvane is compliant with all federal, state, and local laws and is committed to the professional and fair treatment of consumers.&nbsp; Our goal is to assist consumers in resolving their obligations in the manner that best meets their needs and to provide information necessary in order for consumers to make an informed decision. Sed ut perspiciatis unde omnis iste natus error sit voluptatem accusantium doloremque lauda ntim, totam rem aperiam, eaque ipsa quae ab illo invenue lauda ntim, totam rem aperitore veritatis et quasi archi.</p>
  <div class="abs btn" style="left:435px;top:628px"><span class="label">READ MORE</span><span class="arrow"><svg width="9" height="9" viewBox="0 0 10 10"><circle cx="5" cy="5" r="5" fill="#fff"/><path d="M4 3 L6 5 L4 7" stroke="#262a6f" stroke-width="1.5" fill="none"/></svg></span></div>
  <div class="abs divider"></div>
</section>

<section>
  <h2 class="abs section-title" style="left:128px">Consumer <span class="accent">Information</span></h2>
  <div class="abs thumb thumb-meeting" style="left:129px;top:733px" role="img" aria-label="Photo of colleagues gathered around a meeting table"></div>
  <p class="abs col-text" style="left:302px"><span>Sed ut perspiciatis unde omnis iste natus</span><span>error sit voluptatem accusantium dolo-</span><span>remque laudantium, totam rem aperiam,</span><span>ea que ipsa quae ab illo inventore veritatis</span><span>et quasi architectobea tae vitae dicta sunt</span><span class="last">explicaboemo enim ipsam volupta</span></p>
  <div class="abs btn" style="left:302px;top:834px"><span class="label">READ MORE</span><span class="arrow"><svg width="9" height="9" viewBox="0 0 10 10"><circle cx="5" cy="5" r="5" fill="#fff"/><path d="M4 3 L6 5 L4 7" stroke="#262a6f" stroke-width="1.5" fill="none"/></svg></span></div>

  <h2 class="abs section-title" style="left:489px">Careers <span class="accent">@ Tolvane</span></h2>
  <div class="abs thumb thumb-team" style="left:489px;top:733px" role="img" aria-label="Photo of two smiling business professionals"></div>
  <p class="abs col-text" style="left:662px"><span>Sed ut perspiciatis unde omnis iste natus</span><span>error sit voluptatem accusantium dolo-</span><span>remque laudantium, totam rem aperiam,</span><span>ea que ipsa quae ab illo inventore veritatis</span><span>et quasi architectobea tae vitae dicta sunt</span><span class="last">explicaboemo enim ipsam volupta</span></p>
  <div class="abs btn" style="left:662px;top:834px"><span class="label">READ MORE</span><span class="arrow"><svg width="9" height="9" viewBox="0 0 10 10"><circle cx="5" cy="5" r="5" fill="#fff"/><path d="M4 3 L6 5 L4 7" stroke="#262a6f" stroke-width="1.5" fill="none"/></svg></span></div>
</section>

<footer>
  <div class="abs footer"></div>
  <div class="abs footer-brand"><span class="dot"></span>Tolvane Inc.</div>
  <div class="abs vrule" style="left:349px"></div>
  <div class="abs vrule" style="left:608px"></div>
  <div class="abs footer-head" style="left:422px">NAVIGATION</div>
  <div class="abs footer-link" style="top:962px">Home</div>
  <div class="abs footer-link" style="top:980px">Consumer Information</div>
  <div class="abs footer-link" style="top:997px">Careers @ Tolvane</div>
  <div class="abs footer-link" style="top:1015px">Contact</div>
  <div class="abs footer-head" style="left:686px">CONTACT US</div>
  <div class="abs footer-item" style="top:960px"><svg width="6" height="8" viewBox="0 0 6 8"><path d="M3 8 L0.5 4 A3 3 0 1 1 5.5 4 Z" fill="#fff"/><circle cx="3" cy="3" r="1" fill="#262a6f"/></svg><span>201 lorem ipsum dolor site,<br>tolvane dummy text,5482</span></div>
  <div class="abs footer-item" style="top:993px"><svg width="7" height="7" viewBox="0 0 10 10"><path d="M2 0 L4 2.5 L3 4 Q4.5 6 6 7 L7.5 6 L10 8 L8.5 10 Q3 9 0 2 Z" fill="#fff"/></svg><span>Phone:&nbsp; 555-014-2280</span></div>
  <div class="abs footer-item" style="top:1009px"><svg width="7" height="6" viewBox="0 0 9 7"><rect width="9" height="7" fill="#fff"/><path d="M0 0 L4.5 4 L9 0" stroke="#262a6f" fill="none"/></svg><span>info@tolvane.example</span></div>
  <div class="abs copy-bar">© 2016 Tolvane. All copyrights are reserved&nbsp; Term of Use, Privay Policy</div>
  <div class="abs badge-a" role="img" aria-label="Trade association membership badge"></div>
  <div class="abs badge-b" role="img" aria-label="Business accreditation badge"></div>
</footer>
</body>
</html>
```